Larkspur Cosmetics Website needs a professional upgrade

I need a new design for an online cosmetics store that looks professional and clean but also has a natural look and feel to it.

The women in the top bar (Image attached) needs to be included and she is on all of our advertising banners/ stands though I would like to come away from the black.

Design Needs:
- 1 x Home Page
- 1 x Products Page

I have plenty more website coming along so hopefully can find someone who I can rely on for a quick turnover :)

Happy designing !

Industry/Entity Type

Store

Number of Pages Required

2 page

Font styles to use
Sans Serif

Requirements
Must have
• - Natural Clean look
Should not have
• - The current black and green colours

```html
<!DOCTYPE html>
<html lang="en">
<head>
<meta charset="utf-8">
<title>Larkspur Cosmetics – Home</title>
<link rel="stylesheet" href="https://fonts.googleapis.com/css2?family=Montserrat:wght@400;500;600&family=Open+Sans:wght@400;600&display=swap">
<style>
:root{
  --purple:#8e36d0;
  --purple-light:#a64ee3;
  --purple-dark:#7426b0;
  --orange:#e07b00;
  --ink:#2b2b2b;
  --grey-text:#6f6f6f;
  --line:#d9d9d9;
  --band:#e9e9e9;
  --white:#ffffff;
  --star:#f0a030;
}
*{box-sizing:border-box;margin:0;padding:0}
html,body{width:1200px;height:2773px;overflow:hidden;background:var(--white)}
body{position:relative;font-family:"Open Sans",Arial,sans-serif;color:var(--ink)}
.abs{position:absolute}

/* header */
.search{left:129px;top:115px;width:268px;height:37px;border:1px solid #c9c9c9;border-radius:19px;font-size:12px;color:#999;padding:10px 18px}
.search svg{position:absolute;right:12px;top:9px}
.brand{left:400px;top:14px;width:400px;text-align:center}
.brand-mark{width:62px;height:62px;border-radius:50%;background:#3a2e1c;margin:0 auto 32px}
.brand-name{font-family:"Montserrat",sans-serif;font-size:24px;font-weight:400;letter-spacing:1px;color:var(--ink);text-transform:uppercase;white-space:nowrap;line-height:28px}
.header-icons{left:890px;top:124px;display:flex;gap:30px;align-items:center}
.cart-count{left:1028px;top:104px;width:20px;height:20px;border-radius:50%;background:#e4e4e4;font-size:10px;text-align:center;line-height:20px;color:#555}

/* nav */
.nav{left:0;top:177px;width:1200px;height:54px;background:linear-gradient(var(--purple-light),var(--purple))}
.nav ul{list-style:none;position:absolute;left:142px;top:0;display:flex;height:54px}
.nav li{font-family:"Montserrat",sans-serif;font-size:14px;font-weight:500;color:var(--white);height:54px;line-height:54px;text-align:center;border-right:1px solid rgba(255,255,255,.35)}
.nav li:last-child{border-right:0}
.nav li.active{background:var(--purple-dark)}

/* hero */
.hero-photo{left:0;top:231px;width:1200px;height:560px;background:linear-gradient(180deg,#c9dce6 0%,#e4ebee 28%,#ebe1d2 55%,#dccab0 100%)}
.hero-product{left:545px;top:430px;width:175px;height:240px;background:linear-gradient(90deg,#f4f4f1 0%,#e9e9e4 45%,#9aaa3e 55%,#6f7f22 100%)}
.hero-portrait{left:730px;top:231px;width:340px;height:440px;background:linear-gradient(160deg,#5a3d2b 0%,#8a6249 18%,#e8c4ae 38%,#f2d7c7 65%,#e9cdb9 100%)}
.hero-title{left:135px;top:355px;font-family:"Montserrat",sans-serif;font-size:41px;font-weight:400;line-height:51px;color:var(--ink)}
.hero-title span{color:var(--purple)}
.btn-solid{background:var(--orange);color:var(--white);font-family:"Montserrat",sans-serif;font-weight:600;font-size:13px;text-align:center;text-transform:uppercase}
.hero-btn{left:135px;top:471px;width:133px;height:39px;line-height:39px}
.dots{display:flex;gap:5px}
.dots i{width:13px;height:13px;border-radius:50%;background:#a9a9a9;display:block}
.dots i:first-child{background:transparent;border:2px solid #a9a9a9}
.hero-dots{left:135px;top:537px}
.hero-wave{left:0;top:671px}

/* category cards */
.card{top:675px;width:305px;height:224px;border:1px solid #ddd;background:var(--white);overflow:hidden}
.card-title{position:absolute;left:25px;top:34px;font-family:"Montserrat",sans-serif;font-size:25px;font-weight:400;line-height:29px;color:var(--ink)}
.card-text{position:absolute;left:25px;top:105px;width:160px;font-size:11px;line-height:17px;color:#888}
.card-btn{position:absolute;left:25px;top:155px;width:106px;height:32px;border:2px solid var(--orange);color:var(--orange);font-family:"Montserrat",sans-serif;font-size:11px;font-weight:600;line-height:28px;text-align:center}
.card-photo{position:absolute;right:0;top:0;width:130px;height:224px}
.card--eczema .card-photo{background:linear-gradient(90deg,#ffffff 0%,#ececec 30%,#2a2a2a 45%,#6b5a2a 70%,#a38a4a 100%)}
.card--acne{background:linear-gradient(100deg,#c99be8,#efe0f8)}
.card--acne .card-title,.card--acne .card-text{color:var(--white)}
.card--acne .card-btn{border-color:var(--purple);color:var(--purple);background:var(--white)}
.card--acne .card-photo{width:150px;background:linear-gradient(180deg,#6b4a36 0%,#e9c6b3 35%,#f3dccf 100%)}
.card--glossary .card-photo{background:linear-gradient(160deg,#f1ede6 0%,#d8c3a2 45%,#c79a5a 65%,#6f9a36 100%)}

/* featured */
.section-title{font-family:"Montserrat",sans-serif;font-size:21px;font-weight:500;color:var(--ink);text-align:center}
.featured-title{left:0;top:958px;width:1200px}
.underline{left:550px;top:993px;width:86px;height:4px;background:var(--purple)}
.arrow-btn{top:964px;width:28px;height:28px;background:#f0f0f0;border-radius:3px}
.arrow-btn svg{position:absolute;left:9px;top:8px}
.product{top:1036px;width:200px;text-align:center}
.product-photo{width:150px;height:196px;margin:0 auto 34px}
.product-photo--serum{background:linear-gradient(90deg,#ffffff 0%,#1f1f1f 18%,#3a3a3a 45%,#8a7434 55%,#5a4a22 85%,#ffffff 100%)}
.product-photo--lotion{background:linear-gradient(90deg,#ffffff 0%,#f1f1f1 15%,#e7e7e7 45%,#7a1e6a 55%,#4a1044 85%,#ffffff 100%)}
.product-photo--set{background:linear-gradient(180deg,#ffffff 0%,#ffffff 25%,#2a2a2a 40%,#f1f1f1 60%,#c9b27a 80%,#ffffff 100%)}
.product-photo--tubes{background:linear-gradient(180deg,#ffffff 0%,#ffffff 20%,#f3f3f3 30%,#e9e0ee 55%,#b06bc0 70%,#1f1f1f 88%,#ffffff 100%)}
.product-name{font-size:17px;color:#444}
.product-price{font-family:"Montserrat",sans-serif;font-size:25px;font-weight:500;margin-top:8px}
.stars{color:var(--star);font-size:12px;letter-spacing:1px;margin-top:2px}
.add-btn{display:inline-block;width:115px;height:30px;line-height:30px;background:var(--purple);color:var(--white);font-family:"Montserrat",sans-serif;font-size:12px;font-weight:500;margin-top:8px}

/* about */
.about{left:0;top:1483px;width:1200px;height:420px;background:linear-gradient(90deg,#ffffff 0%,#f3f3f3 45%,#e6e6e6 100%)}
.about-photo{left:560px;top:1483px;width:640px;height:420px;background:linear-gradient(90deg,rgba(240,240,240,0) 0%,#f1f1f1 20%,#f7f7f5 50%,#e9e9e6 70%,#b58a5a 88%,#c98a3a 100%)}
.about-title{left:135px;top:1557px;font-family:"Montserrat",sans-serif;font-size:34px;font-weight:400;color:var(--ink)}
.about-text{left:135px;top:1621px;width:430px;font-size:13.5px;line-height:29px;color:#444}
.btn-outline{border:2px solid var(--orange);color:var(--orange);font-family:"Montserrat",sans-serif;font-size:12px;font-weight:600;text-align:center;text-transform:uppercase}
.about-btn{left:131px;top:1782px;width:133px;height:39px;line-height:35px}

/* stories */
.stories{left:0;top:1903px;width:1200px;height:370px;background:var(--orange)}
.stories-title{left:0;top:1975px;width:1200px;color:var(--white);font-size:25px}
.quote{left:255px;top:2018px;width:690px;text-align:center;color:var(--white);font-size:16px;line-height:32px}
.quote-mark{top:2008px;font-family:Georgia,serif;font-size:56px;line-height:56px;color:var(--white);font-weight:700}
.quote-name{left:0;top:2127px;width:1200px;text-align:center;color:var(--white);font-size:16px;font-weight:600}
.stories-dots{left:556px;top:2207px}
.stories-dots i{background:var(--white)}
.stories-dots i:first-child{border-color:var(--white);background:transparent}

/* newsletter */
.newsletter{left:0;top:2273px;width:1200px;height:120px;background:var(--band)}
.news-label{left:233px;top:2323px;font-family:"Montserrat",sans-serif;font-size:20px;font-weight:500;white-space:nowrap}
.news-input{left:494px;top:2311px;width:362px;height:45px;background:var(--white);border:1px solid #ddd;font-size:12px;color:#999;padding:14px 16px}
.news-btn{left:856px;top:2311px;width:137px;height:45px;line-height:45px;background:var(--purple);color:var(--white);text-align:center;font-family:"Montserrat",sans-serif;font-size:14px;font-weight:600}

/* footer */
.footer-col{top:2452px}
.footer-col h4{font-family:"Montserrat",sans-serif;font-size:15px;font-weight:600;color:var(--orange);text-transform:uppercase;margin-bottom:22px}
.footer-col li{list-style:none;font-size:12px;color:#666;line-height:25px}
.contact-item{display:flex;gap:10px;font-size:12px;color:#666;line-height:18px;margin-bottom:14px}
.social{left:847px;top:2605px;display:flex;gap:26px}
.social i{display:block;width:20px;height:20px;border-radius:50%;background:#3d5066}
.payments{left:845px;top:2651px;display:flex;gap:8px}
.payments i{display:block;width:42px;height:26px;border:1px solid #ccc;background:#f3f3f3;border-radius:2px}
.footer-rule{left:161px;top:2709px;width:961px;height:1px;background:var(--line)}
.copyright{left:0;top:2729px;width:1200px;text-align:center;font-size:12px;color:#777}
</style>
</head>
<body>

<header>
  <div class="abs search">Search here
    <svg width="18" height="18" viewBox="0 0 18 18"><circle cx="7.5" cy="7.5" r="5.5" fill="none" stroke="#777" stroke-width="2"/><line x1="11.5" y1="11.5" x2="16" y2="16" stroke="#777" stroke-width="2"/></svg>
  </div>
  <div class="abs brand">
    <div class="brand-mark"></div>
    <div class="brand-name">Larkspur Cosmetics</div>
  </div>
  <div class="abs header-icons">
    <svg width="22" height="22" viewBox="0 0 22 22"><rect x="2" y="5" width="14" height="14" fill="none" stroke="#555" stroke-width="1.6"/><path d="M9 13 L18 4 L20 6 L11 15 L8 16 Z" fill="#555"/></svg>
    <svg width="20" height="20" viewBox="0 0 20 20"><circle cx="10" cy="6" r="4" fill="#555"/><path d="M2 19 C2 12 18 12 18 19 Z" fill="#555"/></svg>
    <svg width="30" height="26" viewBox="0 0 30 26"><path d="M2 10 H28 L24 24 H6 Z" fill="#e07b00"/><path d="M9 10 L15 2 L21 10" fill="none" stroke="#e07b00" stroke-width="2"/></svg>
  </div>
  <div class="abs cart-count">0</div>
</header>

<nav class="abs nav">
  <ul>
    <li class="active" style="width:98px">HOME</li>
    <li style="width:121px">ABOUT US</li>
    <li style="width:129px">PRODUCTS</li>
    <li style="width:144px">TREATMENTS</li>
    <li style="width:93px">MEDIA</li>
    <li style="width:188px">SUCCESS STORIES</li>
    <li style="width:143px">CONTACT US</li>
  </ul>
</nav>

<section class="hero">
  <div class="abs hero-photo" role="img" aria-label="Sunlit beach with sand and sea as backdrop"></div>
  <div class="abs hero-portrait" role="img" aria-label="Portrait of the brand model touching her cheek"></div>
  <div class="abs hero-product" role="img" aria-label="Skincare tube and box"></div>
  <h1 class="abs hero-title"><span>Larkspur is Your</span><br>Natural Skin Specialist</h1>
  <div class="abs btn-solid hero-btn">Shop Now</div>
  <div class="abs dots hero-dots"><i></i><i></i><i></i><i></i></div>
  <svg class="abs hero-wave" width="1200" height="121" viewBox="0 0 1200 121" preserveAspectRatio="none"><path d="M0 87 C250 121 450 121 600 121 C750 121 950 121 1200 87 V121 H0 Z" fill="#fff"/></svg>
</section>

<section class="categories">
  <div class="abs card card--eczema" style="left:135px">
    <div class="card-photo" role="img" aria-label="Serum bottle and box"></div>
    <h3 class="card-title">Eczema<br>Treatment</h3>
    <p class="card-text">Mauris vel lacus vitae felis vestibulum volutpat</p>
    <div class="card-btn">SHOP NOW</div>
  </div>
  <div class="abs card card--acne" style="left:455px">
    <div class="card-photo" role="img" aria-label="Woman with clear skin"></div>
    <h3 class="card-title">Acne<br>Treatmemt</h3>
    <p class="card-text">Mauris vel lacus vitae felis vestibulum volutpat</p>
    <div class="card-btn">SHOP NOW</div>
  </div>
  <div class="abs card card--glossary" style="left:767px">
    <div class="card-photo" role="img" aria-label="Natural ingredients with spoon and leaves"></div>
    <h3 class="card-title">Ingredients<br>Glossary</h3>
    <p class="card-text">Mauris vel lacus vitae felis vestibulum volutpat</p>
    <div class="card-btn">SHOP NOW</div>
  </div>
</section>

<section class="featured">
  <h2 class="abs section-title featured-title">FEATURED PRODUCTS</h2>
  <div class="abs underline"></div>
  <div class="abs arrow-btn" style="left:997px"><svg width="10" height="12" viewBox="0 0 10 12"><path d="M7 1 L2 6 L7 11" fill="none" stroke="#333" stroke-width="2"/></svg></div>
  <div class="abs arrow-btn" style="left:1034px"><svg width="10" height="12" viewBox="0 0 10 12"><path d="M3 1 L8 6 L3 11" fill="none" stroke="#333" stroke-width="2"/></svg></div>

  <div class="abs product" style="left:146px">
    <div class="product-photo product-photo--serum" role="img" aria-label="Serum bottle with gold box"></div>
    <div class="product-name">Revitalising serum</div>
    <div class="product-price">$69.00</div>
    <div class="stars">★★★★★</div>
    <div class="add-btn">Add to Cart</div>
  </div>
  <div class="abs product" style="left:377px">
    <div class="product-photo product-photo--lotion" role="img" aria-label="Hand and body lotion tube with purple box"></div>
    <div class="product-name">Hand &amp; body lotion</div>
    <div class="product-price">$69.00</div>
    <div class="stars">★★★★★</div>
    <div class="add-btn">Add to Cart</div>
  </div>
  <div class="abs product" style="left:610px">
    <div class="product-photo product-photo--set" role="img" aria-label="Serum bottles and cream jar set"></div>
    <div class="product-name">Revitalising serum</div>
    <div class="product-price">$69.00</div>
    <div class="stars">★★★★★</div>
    <div class="add-btn">Add to Cart</div>
  </div>
  <div class="abs product" style="left:841px">
    <div class="product-photo product-photo--tubes" role="img" aria-label="Three skincare tubes"></div>
    <div class="product-name">Revitalising serum</div>
    <div class="product-price">$69.00</div>
    <div class="stars">★★★★★</div>
    <div class="add-btn">Add to Cart</div>
  </div>
</section>

<section class="about-section">
  <div class="abs about"></div>
  <div class="abs about-photo" role="img" aria-label="Jar of white cream with orchid flower on woven mat"></div>
  <h2 class="abs about-title">About Larkspur</h2>
  <p class="abs about-text">Larkspur Cosmetics produces a range of premium natural skincare products based on the healing and soothing Aloe Vera plant to assist people with eczema, psoriasis, dermatitis, acne, pigmentation and those looking for effective natural skincare and daily tonic.</p>
  <div class="abs btn-outline about-btn">Read More</div>
</section>

<section class="success">
  <div class="abs stories"></div>
  <h2 class="abs section-title stories-title">SUCCESS STORIES</h2>
  <div class="abs quote-mark" style="left:222px">“</div>
  <p class="abs quote">I have thick curly hair and had persistent problems with a dry flaky scalp. Using the Larkspur Cosmetics Gel as a shampoo has stopped the itching and flaking and the embarrassing dandruff that resulted</p>
  <div class="abs quote-mark" style="left:938px">”</div>
  <div class="abs quote-name">Dana Whitfield, Ridgeway NSW</div>
  <div class="abs dots stories-dots"><i></i><i></i><i></i><i></i></div>
</section>

<section class="signup">
  <div class="abs newsletter"></div>
  <div class="abs news-label">NEWSLETTER SIGN UP</div>
  <div class="abs news-input">Your Email</div>
  <div class="abs news-btn">SUBSCRIBE</div>
</section>

<footer>
  <div class="abs footer-col" style="left:161px">
    <h4>Information</h4>
    <ul><li>About Us</li><li>Customer Service</li><li>Privacy Policy</li><li>Site Map</li><li>Search Terms</li><li>Orders and Returns</li></ul>
  </div>
  <div class="abs footer-col" style="left:375px">
    <h4>Why Buy From Us</h4>
    <ul><li>Shipping &amp; Returns</li><li>Secure Shopping</li><li>International Shipping</li><li>Affiliates</li><li>Group Sales</li></ul>
  </div>
  <div class="abs footer-col" style="left:625px">
    <h4>My Account</h4>
    <ul><li>Sign In</li><li>View Cart</li><li>My Wishlist</li><li>Track My Order</li><li>Help</li></ul>
  </div>
  <div class="abs footer-col" style="left:847px">
    <h4>Contact Us</h4>
    <div class="contact-item">
      <svg width="14" height="18" viewBox="0 0 14 18"><path d="M7 0 C3 0 0 3 0 7 C0 12 7 18 7 18 C7 18 14 12 14 7 C14 3 11 0 7 0 Z" fill="#555"/><circle cx="7" cy="7" r="2.5" fill="#fff"/></svg>
      <span>214 Meadow Lane Suite<br>B2 Fernhill, PA 19000</span>
    </div>
    <div class="contact-item">
      <svg width="14" height="16" viewBox="0 0 14 16"><path d="M3 0 L6 4 L4 6 C5 9 7 11 10 12 L12 10 L14 13 L11 16 C5 15 0 9 0 3 Z" fill="#555"/></svg>
      <span>(555) 014-2000</span>
    </div>
    <div class="contact-item">
      <svg width="16" height="12" viewBox="0 0 16 12"><rect width="16" height="12" fill="#555"/><path d="M0 0 L8 7 L16 0" fill="none" stroke="#fff" stroke-width="1.5"/></svg>
      <span>hello@larkspur.example</span>
    </div>
  </div>
  <div class="abs social"><i></i><i></i><i></i><i></i></div>
  <div class="abs payments"><i></i><i></i><i></i><i></i><i></i></div>
  <div class="abs footer-rule"></div>
  <div class="abs copyright">© 2016 Larkspur Cosmetics &nbsp;All right reserved &nbsp;Term of Use</div>
</footer>

</body>
</html>
```